Business card for event manager / organizer "waiter service"

Draft of a new valuable business card for my company.
Events, personnel service providers, festivals

```html
<!DOCTYPE html>
<html lang="de">
<head>
<meta charset="utf-8">
<title>Jonas´ Servicecrew – Visitenkarte</title>
<link href="https://fonts.googleapis.com/css2?family=Arimo:wght@400;700&display=swap" rel="stylesheet">
<style>
  :root {
    --bg: #e9e9e9;
    --card: #333333;
    --white: #ffffff;
    --orange: #f07c1b;
    --grey-text: #d8d8d8;
  }
  * { box-sizing: border-box; margin: 0; padding: 0; }
  html, body { width: 1200px; height: 802px; overflow: hidden; }
  body {
    background: var(--bg);
    font-family: "Arimo", Arial, sans-serif;
    display: flex;
    align-items: center;
    justify-content: center;
    gap: 40px;
  }
  .card {
    position: relative;
    width: 540px;
    height: 310px;
    background: var(--card);
    overflow: hidden;
    box-shadow: 0 8px 20px rgba(0,0,0,0.25);
  }

  /* Front side */
  .portrait {
    position: absolute;
    right: 0; top: 0;
    width: 250px; height: 310px;
    background: radial-gradient(ellipse at 45% 35%, #3a3a3d 0%, #1c1e24 55%, #141518 100%);
  }
  .front-content {
    position: absolute;
    left: 36px; top: 40px;
    width: 240px;
  }
  .brand-small {
    display: flex;
    align-items: center;
    gap: 10px;
  }
  .brand-mark {
    width: 32px; height: 32px;
    background: var(--orange);
    flex: none;
  }
  .brand-small .brand-name {
    color: var(--white);
    font-weight: 700;
    font-size: 15px;
    line-height: 1;
    letter-spacing: 0.3px;
    white-space: nowrap;
  }
  .brand-small .tagline {
    color: var(--grey-text);
    font-size: 7.5px;
    margin-top: 4px;
    white-space: nowrap;
  }
  .person { margin-top: 28px; }
  .person-name {
    color: var(--orange);
    font-weight: 700;
    font-size: 21px;
  }
  .person-role {
    color: var(--white);
    font-size: 13px;
    margin-top: 2px;
  }
  .contact-list {
    list-style: none;
    margin-top: 18px;
  }
  .contact-list li {
    display: flex;
    align-items: center;
    gap: 9px;
    color: var(--white);
    font-size: 12.5px;
    line-height: 19px;
    white-space: nowrap;
  }
  .contact-list svg { width: 11px; height: 11px; flex: none; }
  .contact-list .address { padding-left: 20px; }

  /* Back side */
  .back { display: flex; align-items: center; justify-content: flex-end; }
  .back-brand {
    margin-right: 40px;
  }
  .back-brand .brand-name {
    color: var(--white);
    font-weight: 700;
    font-size: 44px;
    line-height: 1.05;
    letter-spacing: 1px;
  }
  .back-brand .tagline {
    color: var(--grey-text);
    font-size: 12px;
    margin-top: 8px;
  }
</style>
</head>
<body>

  <section class="card front">
    <div class="portrait" role="img" aria-label="Porträtfoto des Inhabers in dunklem Hemd vor dunklem Hintergrund"></div>
    <div class="front-content">
      <div class="brand-small">
        <div class="brand-mark"></div>
        <div>
          <div class="brand-name">JONAS´ SERVICECREW</div>
          <div class="tagline">...damit jedes Fest ein Erfolg wird!</div>
        </div>
      </div>
      <div class="person">
        <div class="person-name">Jonas Werbeck</div>
        <div class="person-role">Inhaber</div>
      </div>
      <ul class="contact-list">
        <li>
          <svg viewBox="0 0 12 12"><path fill="#f07c1b" d="M2.5 0.5l2 2.2-1 1.3c.6 1.5 1.8 2.7 3.3 3.3l1.3-1 2.2 2-1.4 1.9C5 10 1.8 6.8 0.6 2z"/></svg>
          02361 555 01 24
        </li>
        <li>
          <svg viewBox="0 0 12 12"><path fill="#f07c1b" d="M2.5 0.5l2 2.2-1 1.3c.6 1.5 1.8 2.7 3.3 3.3l1.3-1 2.2 2-1.4 1.9C5 10 1.8 6.8 0.6 2z"/></svg>
          0151 555 48 37
        </li>
        <li>
          <svg viewBox="0 0 12 12"><rect x="0.5" y="2" width="11" height="8" fill="#f07c1b"/><path d="M0.5 2l5.5 4.5L11.5 2" stroke="#333" stroke-width="1" fill="none"/></svg>
          info@jonas-servicecrew.de
        </li>
        <li>
          <svg viewBox="0 0 12 12"><circle cx="6" cy="6" r="5.2" fill="none" stroke="#f07c1b" stroke-width="1.4"/><ellipse cx="6" cy="6" rx="2.2" ry="5.2" fill="none" stroke="#f07c1b" stroke-width="1"/><path d="M1 6h10" stroke="#f07c1b" stroke-width="1"/></svg>
          www.jonas-servicecrew.de
        </li>
        <li>
          <svg viewBox="0 0 12 12"><circle cx="6" cy="6" r="5.5" fill="#f07c1b"/></svg>
          jonasservicecrew
        </li>
        <li class="address">Birkenweg 12, 45701 Musterstadt</li>
      </ul>
    </div>
  </section>

  <section class="card back">
    <div class="back-brand">
      <div class="brand-name">JONAS´<br>SERVICECREW</div>
      <div class="tagline">...damit jedes Fest ein Erfolg wird!</div>
    </div>
  </section>

</body>
</html>
```